E learning Platform for privacy

Current website is as below and its more of a shell.
I need someone to take the text and content and design it properly.
https://study.vornaquill.com/

After that, design has to be implemented with elementor and wordpress
https://elementor.com/

```html
<!DOCTYPE html>
<html lang="en">
<head>
<meta charset="utf-8">
<title>Vornaquill Learning Centre</title>
<link href="https://fonts.googleapis.com/css2?family=Arimo:wght@400;700&family=Archivo+Black&display=swap" rel="stylesheet">
<style>
:root{
  --orange:#f08a16;
  --ink:#1f1f1f;
  --text:#555;
  --muted:#888;
  --paper:#ffffff;
  --mist:#f5f5f5;
  --line:#d6d6d6;
  --footer:#6e6e6e;
  --footer-deep:#4e4e4e;
  --hero-a:#2c2b30;
  --hero-b:#6b6670;
  --photo-a:#4b4038;
  --photo-b:#c9bfb3;
}
*{box-sizing:border-box;margin:0;padding:0}
html,body{width:1200px;height:3901px;overflow:hidden}
body{font-family:"Arimo",Arial,sans-serif;color:var(--ink);background:var(--paper);position:relative}
.abs{position:absolute}
a{color:inherit;text-decoration:none}

/* header */
.site-header{position:absolute;top:0;left:0;width:1200px;height:79px;background:var(--paper)}
.brand{position:absolute;left:111px;top:14px;width:200px}
.brand-name{font-weight:700;font-size:30px;letter-spacing:2px;color:var(--orange);line-height:34px}
.brand-sub{font-size:8px;letter-spacing:6px;color:var(--ink);margin-top:2px}
.nav a{position:absolute;top:37px;font-size:11px;color:var(--ink)}
.nav .active::before{content:"";position:absolute;left:-2px;right:-2px;top:-10px;height:2px;background:var(--orange)}
.btn-register{position:absolute;left:971px;top:27px;width:115px;height:32px;background:var(--orange);color:#fff;font-size:11px;display:flex;align-items:center;justify-content:center}

/* hero */
.hero{position:absolute;top:79px;left:0;width:1200px;height:542px}
.hero-photo{position:absolute;inset:0;background:linear-gradient(100deg,var(--hero-a) 0%,#3d3a42 45%,var(--hero-b) 75%,#8e8892 100%)}
.hero-title{position:absolute;left:109px;top:166px;font-size:45px;font-weight:700;line-height:44px;color:#fff;letter-spacing:.5px}
.hero-lead{position:absolute;left:112px;top:270px;font-size:13px;color:#fff}
.btn-outline-hero{position:absolute;left:111px;top:304px;width:131px;height:35px;border:2px solid var(--orange);color:#fff;font-size:13px;display:flex;align-items:center;justify-content:center}

/* section shared */
.rule{position:absolute;height:5px;width:219px;background:var(--orange)}
.section-title{position:absolute;font-size:28px;font-weight:700;color:var(--ink);line-height:32px}
.section-lead{position:absolute;width:545px;font-size:13px;line-height:17px;color:var(--text);text-align:justify}

/* courses */
.arrow-btn{position:absolute;top:789px;width:40px;height:38px;border:1px solid var(--line);background:#fff;color:var(--orange);font-size:20px;font-weight:700;display:flex;align-items:center;justify-content:center}
.chat-tab{position:absolute;left:1110px;top:694px;width:90px;height:66px}
.course-card{position:absolute;top:845px;width:229px;height:317px;background:#fff;border:1px solid #e3e3e3;box-shadow:0 1px 5px rgba(0,0,0,.12)}
.course-photo{position:absolute;left:14px;top:14px;width:201px;height:114px;background:linear-gradient(135deg,var(--photo-a),var(--photo-b))}
.course-name{position:absolute;left:0;right:0;top:150px;text-align:center;font-size:13px;color:var(--ink)}
.course-text{position:absolute;left:22px;right:22px;top:175px;font-size:8.5px;line-height:10px;color:var(--text);text-align:justify}
.course-meta{position:absolute;left:22px;font-size:8.5px;color:var(--text)}
.course-meta.price{color:var(--orange);top:245px}

/* stats */
.stats{position:absolute;top:1194px;left:0;width:1200px;height:291px;background:linear-gradient(90deg,#2e2e33,#3e3d44 40%,#55535a 60%,#2f2f34)}
.stat-label{position:absolute;top:68px;font-size:18px;color:#eee;text-align:center;width:300px}
.stat-value{position:absolute;top:100px;font-family:"Archivo Black","Arimo",sans-serif;font-size:92px;line-height:100px;color:var(--orange);text-align:center;width:360px}

/* why */
.why{position:absolute;top:1485px;left:0;width:1200px;height:1007px;background:var(--mist)}
.feature-icon{position:absolute;width:70px;height:70px}
.feature-title{position:absolute;width:280px;font-size:18px;line-height:22px;text-align:center;color:var(--ink)}
.feature-text{position:absolute;width:230px;font-size:11px;line-height:15px;text-align:justify;text-align-last:center;color:var(--text)}
.btn-outline{position:absolute;width:131px;height:37px;border:1px solid var(--orange);color:var(--orange);font-size:13px;display:flex;align-items:center;justify-content:center;background:transparent}

/* blog */
.post-day{position:absolute;font-size:30px;color:var(--orange)}
.post-day small{font-size:12px;margin-left:6px}
.post-year{position:absolute;font-size:17px;color:var(--orange)}
.btn-read{position:absolute;width:88px;height:23px;border:1px solid var(--ink);border-radius:12px;font-size:8px;color:var(--orange);display:flex;align-items:center;justify-content:center}
.post-title{position:absolute;left:374px;font-size:18px;font-weight:700;color:var(--orange)}
.post-text{position:absolute;left:374px;width:338px;font-size:13px;line-height:16.5px;color:var(--text);text-align:justify}
.post-photo{position:absolute;left:797px;width:201px;background:linear-gradient(135deg,var(--photo-a),var(--photo-b))}

/* testimonials */
.testimonials{position:absolute;top:3038px;left:0;width:1200px;height:556px;background:var(--mist)}
.quote-card{position:absolute;top:129px;width:324px;height:313px;border:1px solid #777;border-radius:26px;background:var(--mist)}
.quote-card.featured{background:var(--orange);border-color:var(--orange)}
.quote-mark{position:absolute;left:46px;top:-22px;font-family:"Archivo Black",sans-serif;font-size:50px;line-height:50px;color:var(--orange)}
.featured .quote-mark{color:var(--ink)}
.quote-text{position:absolute;left:30px;right:30px;top:45px;font-size:15px;line-height:16.5px;color:var(--text);text-align:center}
.featured .quote-text{color:#fff}
.quote-photo{position:absolute;left:47px;top:198px;width:97px;height:97px;background:linear-gradient(135deg,#8c7a6b,#d7cfc6)}
.quote-name{position:absolute;left:161px;top:231px;font-size:15px;color:var(--text)}
.quote-role{position:absolute;left:161px;top:256px;font-size:8px;color:var(--muted)}
.featured .quote-name,.featured .quote-role{color:#fff}
.dot{position:absolute;top:3548px;width:10px;height:10px;border:1px solid #666;border-radius:50%}
.dot.on{background:var(--orange);border-color:var(--orange);width:14px;height:14px;top:3546px}

/* footer */
.site-footer{position:absolute;top:3626px;left:0;width:1200px;height:275px;background:var(--footer);color:#fff}
.footer-brand{position:absolute;left:111px;top:30px;font-size:36px;font-weight:700;letter-spacing:4px;color:#fff;line-height:40px}
.footer-brand-sub{position:absolute;left:124px;top:73px;font-size:8px;letter-spacing:7px;color:#fff}
.footer-head{position:absolute;top:40px;font-size:14px;font-weight:700}
.footer-link{position:absolute;font-size:11px}
.footer-link.lg{font-size:14px}
.social{position:absolute;top:71px;width:27px;height:27px;border:2px solid #fff;border-radius:3px}
.legal{position:absolute;top:213px;font-size:9px}
.legal-sep{position:absolute;top:209px;width:1px;height:16px;background:#fff}
.badge{position:absolute;left:112px;top:190px;width:76px;height:25px;background:#dfe6ef;border:1px solid #fff}
.footer-bottom{position:absolute;left:0;top:230px;width:1200px;height:45px;background:var(--footer-deep);font-size:10px}
</style>
</head>
<body>

<header class="site-header">
  <div class="brand">
    <div class="brand-name">VORNAQUILL</div>
    <div class="brand-sub">LEARNING CENTRE</div>
  </div>
  <nav class="nav">
    <a class="active" style="left:415px">HOME</a>
    <a style="left:494px">BLOGS</a>
    <a style="left:579px">COURSES</a>
    <a style="left:683px">CONTACT US</a>
    <a style="left:805px">ABOUT US</a>
    <a style="left:910px">SIGN IN</a>
  </nav>
  <a class="btn-register">REGISTER</a>
</header>

<section class="hero">
  <div class="hero-photo" role="img" aria-label="Photo of a student writing notes in a lecture hall"></div>
  <h1 class="hero-title">DATA PROTECTION<br>EXCELLENCE</h1>
  <p class="hero-lead">Largest online e-learning resource for data protection &amp; privacy</p>
  <a class="btn-outline-hero">Get Trained</a>
</section>

<!-- featured courses -->
<div class="rule" style="left:111px;top:677px"></div>
<h2 class="section-title" style="left:109px;top:704px">FEATURED COURSES</h2>
<p class="section-lead" style="left:109px;top:750px">Lorem Ipsum is simply dummy text of the printing and typesetting industry. Lorem Ipsum has been the industry's standard dummy text ever since the 1500s, when an unknown printer took a galley of type and scrambled it to make a type</p>
<a class="arrow-btn" style="left:953px">&#10094;</a>
<a class="arrow-btn" style="left:1009px">&#10095;</a>
<svg class="chat-tab" viewBox="0 0 90 66" aria-hidden="true">
  <path d="M30 0 H90 V66 H30 Q18 66 18 54 V42 L0 33 L18 26 V12 Q18 0 30 0Z" fill="var(--orange)"/>
  <rect x="42" y="26" width="24" height="17" rx="8" fill="none" stroke="#fff" stroke-width="2"/>
  <rect x="56" y="16" width="24" height="17" rx="8" fill="var(--orange)" stroke="#fff" stroke-width="2"/>
  <line x1="47" y1="34" x2="60" y2="34" stroke="#fff" stroke-width="1.5"/>
  <line x1="61" y1="25" x2="75" y2="25" stroke="#fff" stroke-width="1.5"/>
</svg>

<article class="course-card" style="left:106px">
  <div class="course-photo" role="img" aria-label="Photo of three women working together at a laptop"></div>
  <h3 class="course-name">How to Scale Social Impact</h3>
  <p class="course-text">Lorem Ipsum is simply dummy text of the printing and typesetting industry. Lorem Ipsum has been the industry's standard dummy text ever since the 1500s, when an</p>
  <p class="course-meta price">FREE</p>
  <p class="course-meta" style="top:265px">DEC 19, 2019</p>
  <p class="course-meta" style="top:285px">CSS</p>
</article>
<article class="course-card" style="left:360px">
  <div class="course-photo" role="img" aria-label="Photo of a team meeting at a white table"></div>
  <h3 class="course-name">Openmark Demonstration Course</h3>
  <p class="course-text">Lorem Ipsum is simply dummy text of the printing and typesetting industry. Lorem Ipsum has been the industry's standard dummy text ever since the 1500s, when an</p>
  <p class="course-meta price">FREE</p>
  <p class="course-meta" style="top:265px">DEC 19, 2019</p>
  <p class="course-meta" style="top:285px">CSS</p>
</article>
<article class="course-card" style="left:615px">
  <div class="course-photo" role="img" aria-label="Photo of a team meeting at a white table"></div>
  <h3 class="course-name">Gobal Social Entrepreneurship</h3>
  <p class="course-text">Lorem Ipsum is simply dummy text of the printing and typesetting industry. Lorem Ipsum has been the industry's standard dummy text ever since the 1500s, when an</p>
  <p class="course-meta price">FREE</p>
  <p class="course-meta" style="top:265px">DEC 19, 2019</p>
  <p class="course-meta" style="top:285px">CSS</p>
</article>
<article class="course-card" style="left:864px">
  <div class="course-photo" role="img" aria-label="Photo of a team meeting at a white table"></div>
  <h3 class="course-name">Openmark Demonstration Course</h3>
  <p class="course-text">Lorem Ipsum is simply dummy text of the printing and typesetting industry. Lorem Ipsum has been the industry's standard dummy text ever since the 1500s, when an</p>
  <p class="course-meta price">FREE</p>
  <p class="course-meta" style="top:265px">DEC 19, 2019</p>
  <p class="course-meta" style="top:285px">CSS</p>
</article>

<!-- stats -->
<section class="stats" role="img" aria-label="Dark photo of an open textbook behind the statistics">
  <p class="stat-label" style="left:138px">ENROLLED STUDENTS</p>
  <p class="stat-value" style="left:88px">6,375</p>
  <p class="stat-label" style="left:491px;top:62px">LESSONS</p>
  <p class="stat-value" style="left:464px">114</p>
  <p class="stat-label" style="left:826px">VIDEOS</p>
  <p class="stat-value" style="left:780px">169</p>
</section>

<!-- why -->
<section class="why">
  <div class="rule" style="left:109px;top:78px"></div>
  <h2 class="section-title" style="left:109px;top:102px">WHY THE (VORNAQUILL) LEARNING<br>CENTRE?</h2>
  <p class="section-lead" style="left:109px;top:179px">Our mission at the Vornaquill Privacy Learning Centre is to provide business and job opportunities, as well as to enhance personal and career advancement for data protection / privacy professionals.</p>

  <svg class="feature-icon" style="left:227px;top:280px" viewBox="0 0 70 70" aria-hidden="true">
    <circle cx="35" cy="35" r="30" fill="none" stroke="var(--orange)" stroke-width="2.5"/>
    <path d="M48 22 L20 33 L32 37 L36 50 Z M32 37 L48 22" fill="none" stroke="var(--orange)" stroke-width="2.5" stroke-linejoin="round"/>
  </svg>
  <h3 class="feature-title" style="left:118px;top:403px">Comprehensive Roadmap</h3>
  <p class="feature-text" style="left:145px;top:459px">Our objective is to provide a comprehensive competency roadmap, instead of one-off courses, whether you are a new or experienced officer, or an individual pursuing a career in data protection.</p>

  <svg class="feature-icon" style="left:548px;top:278px" viewBox="0 0 70 70" aria-hidden="true">
    <g fill="none" stroke="var(--orange)" stroke-width="2.5">
      <circle cx="35" cy="35" r="18"/>
      <path d="M35 5v9M35 56v9M5 35h9M56 35h9M14 14l6 6M50 50l6 6M14 56l6-6M50 20l6-6"/>
      <circle cx="35" cy="35" r="24" stroke-dasharray="6 5"/>
      <path d="M27 35l6 6 11-12"/>
    </g>
  </svg>
  <h3 class="feature-title" style="left:448px;top:403px">Operational Perspective</h3>
  <p class="feature-text" style="left:473px;top:459px">We cover a broad range of data protection topics from both a legal and operational perspective, covering multiple jurisdictions and drawing from enforcement cases around the world and practical scenarios.</p>

  <svg class="feature-icon" style="left:880px;top:280px" viewBox="0 0 70 70" aria-hidden="true">
    <path d="M2 24 L35 10 L68 24 L35 38 Z" fill="var(--orange)"/>
    <path d="M16 31 V44 Q35 54 54 44 V31 L35 40 Z" fill="var(--orange)"/>
    <path d="M62 27 V50" stroke="var(--ink)" stroke-width="2"/>
    <rect x="59" y="50" width="6" height="8" fill="var(--ink)"/>
  </svg>
  <h3 class="feature-title" style="left:787px;top:394px">Academic &amp; International Certification</h3>
  <p class="feature-text" style="left:813px;top:463px">We partner with prominent universities in the region as well as international certification bodies such as the Global Guild of Privacy Practitioners (GGPP).</p>

  <svg class="feature-icon" style="left:218px;top:603px" viewBox="0 0 70 70" aria-hidden="true">
    <g fill="none" stroke="var(--orange)" stroke-width="2.5">
      <path d="M24 42 Q16 34 16 26 A19 19 0 0 1 54 26 Q54 34 46 42 V50 H24 Z"/>
      <path d="M26 56 H44 M29 62 H41"/>
      <path d="M35 16 V34 M35 38 V40"/>
      <path d="M35 0v4M4 26h5M61 26h5M12 6l4 4M58 6l-4 4M10 46l4-3M60 46l-4-3"/>
    </g>
  </svg>
  <h3 class="feature-title" style="left:118px;top:734px">Network with other peers</h3>
  <p class="feature-text" style="left:145px;top:798px">Participate in our online communities and discussion rooms and your network with other like-minded course participants; share best practices, discuss requirements or seek help.</p>

  <svg class="feature-icon" style="left:550px;top:603px" viewBox="0 0 70 70" aria-hidden="true">
    <g fill="none" stroke="var(--orange)" stroke-width="2.5">
      <circle cx="35" cy="35" r="14"/>
      <circle cx="35" cy="35" r="21"/>
      <path d="M35 2v12M35 56v12M2 35h12M56 35h12M11 11l8 8M51 51l8 8M11 59l8-8M51 19l8-8"/>
      <circle cx="35" cy="3" r="3"/><circle cx="35" cy="67" r="3"/><circle cx="3" cy="35" r="3"/><circle cx="67" cy="35" r="3"/>
    </g>
    <text x="35" y="41" text-anchor="middle" font-family="Arimo,sans-serif" font-weight="700" font-size="17" fill="var(--orange)">$</text>
  </svg>
  <h3 class="feature-title" style="left:448px;top:726px">Business and Job<br>Opportunities</h3>
  <p class="feature-text" style="left:473px;top:797px">Collaborate with other professionals on potential business opportunities whether it relates to consultancy, legal or training services.</p>

  <svg class="feature-icon" style="left:893px;top:603px" viewBox="0 0 70 70" aria-hidden="true">
    <g fill="none" stroke="var(--orange)" stroke-width="4" stroke-linecap="round">
      <circle cx="12" cy="54" r="6"/>
      <path d="M6 32 A26 26 0 0 1 34 60"/>
      <path d="M6 18 A40 40 0 0 1 48 60"/>
      <path d="M6 4 A54 54 0 0 1 62 60"/>
    </g>
  </svg>
  <h3 class="feature-title" style="left:785px;top:726px">Modular Approach &amp;<br>Flexibility</h3>
  <p class="feature-text" style="left:813px;top:797px">All our courses are modular in nature to cater to the busy professional, meaning that you can take the courses separately first at your own pace, and then work your way up.</p>

  <a class="btn-outline" style="left:527px;top:916px">Learn More</a>
</section>

<!-- blog -->
<div class="rule" style="left:111px;top:2528px"></div>
<h2 class="section-title" style="left:111px;top:2554px">BLOG</h2>
<p class="section-lead" style="left:111px;top:2603px">Lorem Ipsum is simply dummy text of the printing and typesetting industry. Lorem Ipsum has been the industry's standard dummy text ever since the 1500s, when an unknown printer took a galley of type and scrambled it to make a type</p>

<p class="post-day" style="left:201px;top:2696px">18<small>Dec</small></p>
<p class="post-year" style="left:201px;top:2735px">2019</p>
<a class="btn-read" style="left:226px;top:2766px">Read Full</a>
<h3 class="post-title" style="top:2697px">How To write blog</h3>
<p class="post-text" style="top:2730px">Lorem Ipsum is simply dummy text of the printing and typesetting industry. Lorem Ipsum has been the industry's standard dummy text ever since the 1500s, when an unknown printer took a galley of type and</p>
<div class="post-photo" style="top:2692px;height:114px" role="img" aria-label="Photo of three women reviewing work at a laptop"></div>

<p class="post-day" style="left:201px;top:2837px">24<small>Mar</small></p>
<p class="post-year" style="left:201px;top:2876px">2019</p>
<a class="btn-read" style="left:226px;top:2905px">Read Full</a>
<h3 class="post-title" style="top:2828px">Hello World</h3>
<p class="post-text" style="top:2870px">Lorem Ipsum is simply dummy text of the printing and typesetting industry. Lorem Ipsum has been the industry's standard dummy text ever since the 1500s, when an unknown printer took a galley of type and</p>
<div class="post-photo" style="top:2833px;height:115px;background:linear-gradient(135deg,#cfcac4,#8d8279)" role="img" aria-label="Photo of a bright office meeting around a table"></div>

<a class="btn-outline" style="left:527px;top:2974px">View All</a>

<!-- testimonials -->
<section class="testimonials">
  <h2 class="section-title" style="left:0;width:1200px;text-align:center;top:50px">WHAT PEOPLE SAY</h2>

  <article class="quote-card" style="left:70px">
    <span class="quote-mark">&ldquo;</span>
    <p class="quote-text">Lorem Ipsum is simply dummy text of the printing and typesetting industry. Lorem Ipsum has been the industry's standard dummy text ever since the 1500s, when an unknown printer took a galley of type and scrambled it to make a type</p>
    <div class="quote-photo" role="img" aria-label="Portrait photo of a smiling young man"></div>
    <p class="quote-name">Marcus</p>
    <p class="quote-role">Software Engineering, Norvel</p>
  </article>
  <article class="quote-card featured" style="left:421px">
    <span class="quote-mark">&ldquo;</span>
    <p class="quote-text">Lorem Ipsum is simply dummy text of the printing and typesetting industry. Lorem Ipsum has been the industry's standard dummy text ever since the 1500s, when an unknown printer took a galley of type and scrambled it to make a type</p>
    <div class="quote-photo" role="img" aria-label="Portrait photo of a man in glasses"></div>
    <p class="quote-name">Marcus</p>
    <p class="quote-role">Software Engineering, Norvel</p>
  </article>
  <article class="quote-card" style="left:780px">
    <span class="quote-mark">&ldquo;</span>
    <p class="quote-text">Lorem Ipsum is simply dummy text of the printing and typesetting industry. Lorem Ipsum has been the industry's standard dummy text ever since the 1500s, when an unknown printer took a galley of type and scrambled it to make a type</p>
    <div class="quote-photo" role="img" aria-label="Portrait photo of a laughing man"></div>
    <p class="quote-name">Marcus</p>
    <p class="quote-role">Software Engineering, Norvel</p>
  </article>
</section>
<span class="dot" style="left:557px"></span>
<span class="dot" style="left:575px"></span>
<span class="dot on" style="left:591px"></span>
<span class="dot" style="left:611px"></span>

<!-- footer -->
<footer class="site-footer">
  <div class="footer-brand">VORNAQUILL</div>
  <div class="footer-brand-sub">LEARNING CENTRE</div>
  <p class="footer-link" style="left:112px;top:142px;font-size:10px">VORNAQUILL LEARNING CENTRE</p>

  <p class="footer-head" style="left:441px">COMPANY</p>
  <a class="footer-link" style="left:441px;top:80px">COURSES</a>
  <a class="footer-link" style="left:441px;top:113px">ABOUT US</a>
  <a class="footer-link" style="left:441px;top:144px">FAQS</a>

  <p class="footer-head" style="left:668px;top:38px">GET INVOLVED</p>
  <a class="footer-link lg" style="left:668px;top:76px">Blog</a>
  <a class="footer-link lg" style="left:668px;top:108px">Contact</a>

  <p class="footer-head" style="left:918px">CONNECT</p>
  <span class="social" style="left:918px" aria-label="Professional network"></span>
  <span class="social" style="left:953px" aria-label="Social page"></span>
  <span class="social" style="left:989px" aria-label="Microblog"></span>
  <span class="social" style="left:1024px" aria-label="Photo feed"></span>

  <span class="badge" role="img" aria-label="Accessibility conformance badge"></span>

  <a class="legal" style="left:736px">TERMS OF SERVICE</a>
  <span class="legal-sep" style="left:855px"></span>
  <a class="legal" style="left:883px">HONOR CODE</a>
  <span class="legal-sep" style="left:980px"></span>
  <a class="legal" style="left:1009px">PRIVACY POLICY</a>

  <div class="footer-bottom">
    <p class="abs" style="left:111px;top:17px">POWERED BY <span style="font-size:13px;font-weight:700;margin-left:6px">Learnforge</span> <span style="font-size:13px;font-weight:700;margin-left:16px">Openmark</span></p>
    <p class="abs" style="left:0;width:1200px;text-align:center;top:16px">© LEARNFORGE 2019. ALL RIGHTS RESERVED.</p>
    <p class="abs" style="left:1139px;top:17px;font-size:12px">044</p>
  </div>
</footer>

</body>
</html>
```